Quick and easy spring book cover needed

We need a creative book cover design for a spring fiction book. The title of the book is The Lantern Harbor Theory. The author's name is Marcus Whitfield. The book is 4.25 x 7 inch. The spine is .5 inch. It should include the title, the author's name, and the emblem. The emblem should be set at .5 inches in length.
The book summary is as follows:
When Miriam Tolley moves from her homeland in Japan to pursue her dream as an editor in the United States, she soon encounters a young Washingtonian artist. After being given the task to interview him, she becomes fixated on the mystique surrounding his past. She conjures her inner detective skills to embark on, what she thinks is, the biggest story of her career. But will her heart get in her way?
The final design should reflect spring and young love, nothing sexual and overly romantic. The background and font colors should go well with the imagery. I have attached 2 photos in which should be incorporated. The third attachment is the emblem that is to be placed at the bottom of the spine.
Project Deadline Extended
Reason: The deadline has been extended to allow for revisions, in addition the publisher is considering multiple covers for this project.
Detective

```html
<!DOCTYPE html>
<html lang="en">
<head>
<meta charset="utf-8">
<title>The Lantern Harbor Theory — Cover</title>
<link rel="stylesheet" href="https://fonts.googleapis.com/css2?family=Pixelify+Sans:wght@400;500&family=PT+Sans&display=swap">
<style>
  :root {
    --paper: #ffffff;
    --blossom: #e7c3bf;
    --blossom-pale: #f4e1de;
    --blossom-deep: #d9a9a4;
    --magenta: #b2246b;
    --author-pale: #eec8c2;
    --author-spine: #c05a86;
  }
  html, body { margin: 0; padding: 0; overflow: hidden; background: var(--paper); }
  .cover {
    position: relative;
    width: 1200px;
    height: 941px;
    overflow: hidden;
    background: var(--paper);
    font-family: "PT Sans", sans-serif;
  }
  .back {
    position: absolute; left: 0; top: 0; width: 572px; height: 941px;
  }
  .back-photo {
    position: absolute; inset: 0;
    background:
      radial-gradient(ellipse 220px 300px at 380px 560px, var(--blossom-deep), transparent 70%),
      radial-gradient(ellipse 260px 180px at 120px 780px, var(--blossom-deep), transparent 70%),
      linear-gradient(180deg, var(--blossom-pale) 0%, var(--blossom) 55%, var(--blossom-deep) 100%);
  }
  .back-title {
    position: absolute; left: 80px; top: 44px; margin: 0;
    font-family: "Pixelify Sans", monospace; font-weight: 500;
    font-size: 21px; letter-spacing: 1.5px; color: var(--magenta);
  }
  .blurb {
    position: absolute; left: 80px; top: 96px; width: 395px; margin: 0;
    font-size: 18.5px; line-height: 31px; color: var(--paper);
  }
  .spine {
    position: absolute; left: 572px; top: 0; width: 60px; height: 941px;
    background: var(--paper);
  }
  .spine-title, .spine-author {
    position: absolute; left: 50%; margin: 0; white-space: nowrap;
    transform-origin: left top; transform: rotate(90deg) translateY(-50%);
  }
  .spine-title {
    top: 70px;
    font-family: "Pixelify Sans", monospace; font-weight: 500;
    font-size: 26px; letter-spacing: 2px; color: var(--magenta);
  }
  .spine-author {
    top: 612px; font-size: 24px; color: var(--author-spine);
  }
  .emblem {
    position: absolute; left: 50%; top: 832px; transform: translateX(-50%);
    display: flex; flex-direction: column; align-items: center; gap: 5px;
    font-size: 11px; color: var(--author-spine);
  }
  .emblem-mark { width: 14px; height: 14px; border: 2px solid var(--author-spine); }
  .front {
    position: absolute; left: 632px; top: 0; width: 568px; height: 941px;
    background: var(--paper);
  }
  .front-photo {
    position: absolute; left: 20px; top: 300px; width: 540px; height: 470px;
    background:
      radial-gradient(ellipse 150px 120px at 290px 300px, var(--blossom-deep), transparent 75%),
      radial-gradient(ellipse 90px 160px at 150px 170px, var(--blossom), transparent 75%),
      radial-gradient(ellipse 270px 200px at 280px 300px, var(--blossom-pale), transparent 80%);
  }
  .front-title {
    position: absolute; left: 0; top: 50px; width: 100%; margin: 0;
    text-align: center;
    font-family: "Pixelify Sans", monospace; font-weight: 500;
    font-size: 64px; line-height: 76px; color: var(--magenta);
  }
  .front-author {
    position: absolute; left: 0; top: 872px; width: 100%; margin: 0;
    text-align: center; font-size: 25px; color: var(--author-pale);
  }
</style>
</head>
<body>
<div class="cover">
  <section class="back">
    <div class="back-photo" role="img" aria-label="Soft pink-toned photograph of a young couple beneath a blossoming tree in a park"></div>
    <h2 class="back-title">The Lantern Harbor Theory</h2>
    <p class="blurb">When Miriam Tolley moves from her homeland in Japan to pursue her dream as an editor in the United States, she soon encounters a young Washingtonian artist. After being given the task to interview him, she becomes fixated on the mystique surrounding his past. She conjures her inner detective skills to embark on, what she thinks is, the biggest story of her career. But will her heart get in her way?</p>
  </section>

  <section class="spine">
    <p class="spine-title">The Lantern Harbor Theory</p>
    <p class="spine-author">Marcus Whitfield</p>
    <div class="emblem"><span class="emblem-mark"></span><span>Wrenfield</span></div>
  </section>

  <section class="front">
    <div class="front-photo" role="img" aria-label="Faded pink photograph of a couple sitting together under a tree"></div>
    <h1 class="front-title">The<br>Lantern Harbor<br>Theory</h1>
    <p class="front-author">Marcus Whitfield</p>
  </section>
</div>
</body>
</html>
```